Brenlith - IT Consultancy Website

Our company is called Brenlith and our purpose is to help companies sustainably embrace and reap the benefits of cloud platforms, through transforming practices, skills and technology using DevOps and Security practices such that they are able to automate, manage and secure their cloud platforms to deliver product to market with increasing velocity.

To get our business started I require a website that will model the typical layout of an IT consultancy services company to an Australian Market. There are many examples of such a site, here are some of them. We would like a landing page and then a few simple menu options (About, Blog, Services etc..) to additional content

http://pelvo.com.au/
http://www.brisket.com.au/
http://www.tandu.com.au/

I require the site to be created with a separate CSS file that maintains the colour palette. This is a very important requirement, I want to be able to change the colours employed in the site in a single location and not have to scan through multiple files to replace the codes.

The website must be built using static content as it will not be hosted on a web server but instead in QNT using S3 and CloudFront CDN. Therefore please stick to HTML, JavaScript, CSS and other static file formats. The website needs to be response, smooth and reactive. It should render on desktop, mobile and tablet and feature smooth scrolling, transitions and fade in's.

The website should give the customer confidence that they are dealing with a highly professional IT services company, focused strongly on cloud (QNT, Vantrel Skyline, Horvik Vapor etc..), motivated by beautiful and fluid design.

In order to make this simpler for you, the designer, I have already purchased this template from https://skinmarketly.com/theme/the-venture-allround-template-KX7Q41093 and uploaded it. Feel free to use this template if you choose (note that it makes use of a separate color palette which is a key requirement) or use one of your own choosing. If you do use this template ensure that it does not look too much like "another bootstrap site" therefore use the layout and widgets but make the site look fresh and original too.
Obviously you must delete all trace of the bootstrap package once the project has completed if you do use it

Target Market(s)

Corporate and medium enterprise businesses

Industry/Entity Type

Information Technology

Coding

Coded - Design and coding required

Number of Pages Required

4 page

Font styles to use
Sans Serif

Colors
abd036
33a6d7

Requirements
Must have
• The website should give the customer confidence that they are dealing with a highly professional IT services company, focused strongly on cloud (QNT, Vantrel Skyline, Horvik Vapor etc..), motivated by beautiful and fluid design. Our company name is Brenlith, the site needs to pay homage to the themes of fluidity and logic
• Along with About Us, Services and a Blog page could I also get social logo's included too
Nice to have
• The website must be built using static content as it will not be hosted on a web server but instead in QNT using S3 and CloudFront CDN. Therefore please stick to HTML, JavaScript, CSS and other static file formats. The website needs to be response, smooth and reactive. It should render on desktop, mobile and tablet and feature smooth scrolling, transitions and fade in's.
Should not have
• Lurid colours, or too much animations. The design must "flow"

```html
<!DOCTYPE html>
<html lang="en">
<head>
<meta charset="utf-8">
<title>Brenlith IT Consultancy</title>
<link href="https://fonts.googleapis.com/css2?family=Raleway:wght@300;400;500;600;700&family=Open+Sans:wght@400;600&display=swap" rel="stylesheet">
<style>
:root{
  --cyan:#1aa6d8;
  --navy:#1b4f91;
  --band:#134a8e;
  --feature-blue:#3b65a6;
  --feature-dark:#2f2f31;
  --ink:#2b2b2b;
  --body:#6b6b6b;
  --muted:#9a9a9a;
  --line:#e6e6e6;
  --soft:#f7f6f3;
  --white:#ffffff;
  --footer:#232323;
  --gray-head:#8c8c8c;
  --dark-head:#3a3a3a;
  --orange:#f29a1f;
  --azure:#2d7fd0;
}
*{box-sizing:border-box;margin:0;padding:0}
html,body{width:1200px;height:3564px;overflow:hidden}
body{font-family:'Raleway',sans-serif;color:var(--ink);background:var(--white);position:relative}
.abs{position:absolute}
p{font-family:'Open Sans',sans-serif}

/* top bar */
.topbar{top:0;left:0;width:1200px;height:43px;border-top:3px solid var(--cyan);border-bottom:1px solid var(--line);font-size:10px;color:var(--muted)}
.topbar .item{top:12px;display:flex;align-items:center;gap:6px}
.social-dots{top:13px;left:927px;display:flex;gap:9px}
.social-dots span{width:11px;height:11px;background:#b8b8b8;border-radius:2px;display:block}

/* nav */
.nav{top:43px;left:0;width:1200px;height:71px}
.logo{left:188px;top:20px;font-size:21px;color:var(--ink)}
.logo b{font-weight:700}
.menu{top:26px;font-size:11px;font-weight:500;color:#444}
.menu.active{color:var(--cyan)}

/* hero */
.hero{top:114px;left:0;width:1200px;height:499px;background:linear-gradient(90deg,#e9ecef 0%,#f4f5f6 35%,#efe6df 60%,#d9c7b8 80%,#3a3a3e 100%)}
.hero-kicker{left:188px;top:160px;font-size:28px;font-weight:400;color:#333}
.hero-title{left:188px;top:195px;font-size:37px;font-weight:700;color:var(--navy)}
.hero-text{left:188px;top:246px;width:480px;font-size:11px;line-height:16px;color:#555}
.btn{display:flex;align-items:center;justify-content:center;font-size:9.5px;font-weight:700;letter-spacing:.5px;color:var(--white)}
.hero-btn{left:192px;top:320px;width:119px;height:36px;background:var(--cyan)}
.hero-arrow{left:1084px;top:233px}
.hero-dots{left:575px;top:447px;display:flex;gap:6px}
.hero-dots span{width:7px;height:7px;border-radius:50%;border:1px solid #bbb;display:block}

/* welcome */
.welcome{top:613px;left:0;width:1200px;height:333px}
.h2{font-size:29px;font-weight:400;color:var(--ink)}
.welcome .h2{left:188px;top:62px}
.welcome p{left:188px;top:107px;width:480px;font-size:10.5px;line-height:15.5px;color:var(--body)}
.dark-btn{background:#3a3a3a}
.welcome .btn{left:188px;top:242px;width:118px;height:36px}
.phone-back{left:903px;top:100px;width:111px;height:233px;background:var(--white);border-radius:22px 22px 0 0;box-shadow:0 4px 20px rgba(0,0,0,.15)}
.phone-back .scr{position:absolute;left:0;right:14px;top:60px;bottom:0;background:#e3e3e3}
.phone-front{left:713px;top:52px;width:218px;height:281px;background:#2c2c2e;border-radius:28px 28px 0 0}
.phone-front .scr{position:absolute;left:18px;right:18px;top:66px;bottom:0;background:linear-gradient(135deg,#dfe6ee,#9aa8b8 60%,#4d5563)}

/* services */
.services{top:946px;left:0;width:1200px;height:271px;background:var(--soft)}
.services .h2{width:1200px;text-align:center;top:36px}
.svc{top:112px;width:190px}
.svc .brand{display:flex;align-items:center;gap:8px;height:34px;font-size:15px;font-weight:500;color:#3a3a3a}
.svc .brand i{display:block;width:18px;height:18px}
.svc p{margin-top:10px;font-size:9.5px;line-height:13px;color:var(--body)}
.svc .more{margin-top:10px;font-size:9px;color:var(--muted)}
.svc .more.on{color:var(--cyan)}

/* band */
.band{top:1217px;left:0;width:1200px;height:197px;background:var(--band);color:var(--white)}
.band h3{left:188px;top:52px;font-size:27px;font-weight:500}
.band p{left:188px;top:98px;width:560px;font-size:10.5px;line-height:15px;color:#d9e3f1}
.band .btn{left:893px;top:101px;width:121px;height:37px;background:var(--cyan)}

/* features */
.features{top:1414px;left:0;width:1200px;height:660px;background:linear-gradient(90deg,var(--feature-dark) 50%,var(--feature-blue) 50%);color:var(--white)}
.features .our{width:1200px;text-align:center;top:44px;font-size:24px;font-weight:300}
.features .ttl{width:1200px;text-align:center;top:76px;font-size:28px;font-weight:300;letter-spacing:.5px}
.features .ttl b{font-weight:700}
.fphone{left:489px;top:140px;width:219px;height:466px;background:#3b3b3d;border-radius:30px;box-shadow:0 10px 30px rgba(0,0,0,.4)}
.fphone .spk{position:absolute;left:90px;top:32px;width:40px;height:5px;border-radius:3px;background:#222}
.fphone .scr{position:absolute;left:19px;top:66px;width:186px;height:328px;background:linear-gradient(160deg,#dfe8ef,#9fb0c0 45%,#6f5a4e 80%,#b69685)}
.fphone .home{position:absolute;left:88px;top:410px;width:44px;height:44px;border-radius:50%;border:2px solid #2a2a2c}
.feat{width:200px}
.feat h4{font-size:13px;font-weight:700}
.feat p{font-size:9.5px;line-height:12.5px;color:#ddd;margin-top:3px}
.feat.left{text-align:right;left:180px}
.feat.right{left:822px}
.feat.hi h4{color:var(--cyan)}
.feat.hi p{color:#999}
.tri{width:46px;height:46px}

/* pricing */
.pricing{top:2074px;left:0;width:1200px;height:682px;background:var(--soft)}
.pricing .h2{left:188px;top:56px;font-size:28px}
.pricing .lead{left:188px;top:100px;width:480px;font-size:10.5px;line-height:15px;color:var(--body)}
.plan{background:var(--white);box-shadow:0 3px 14px rgba(0,0,0,.1);text-align:center}
.plan .head{color:var(--white);display:flex;flex-direction:column;justify-content:center}
.plan .head h5{font-size:19px;font-weight:700}
.plan .head span{font-size:8.5px;opacity:.8;margin-top:2px}
.plan .price{height:66px;display:flex;align-items:center;justify-content:center;border-bottom:1px solid var(--line);font-size:30px;font-weight:700;color:#3a3a3a}
.plan .price sup{font-size:12px;font-weight:600}
.plan .price small{font-size:12px;vertical-align:top;font-weight:600}
.plan ul{list-style:none;padding-top:12px}
.plan li{font-size:9.5px;color:var(--body);height:28.5px;line-height:28.5px;font-family:'Open Sans',sans-serif}
.plan .btn{margin:0 auto;width:118px;height:37px}
.plan.mid .price{color:#c59a74}

/* blog */
.blog{top:2756px;left:0;width:1200px;height:464px}
.blog .h2{left:188px;top:58px;font-size:29px}
.circ{width:15px;height:15px;border-radius:50%;border:1px solid #ccc}
.post{top:112px;width:262px;height:270px;background:var(--white);box-shadow:0 2px 8px rgba(0,0,0,.06)}
.post .img{height:140px;position:relative}
.post .tag{position:absolute;left:0;top:0;width:26px;height:26px;background:rgba(40,40,40,.75)}
.post .meta{display:flex;gap:22px;padding:14px 12px 0;font-size:8px;color:var(--muted)}
.post h6{padding:12px 12px 0;font-size:14.5px;font-weight:500;color:#333}
.post p{padding:6px 12px 0;font-size:9.5px;line-height:12.5px;color:var(--body)}
.post .more{padding:12px 12px 0;font-size:9px;color:var(--muted)}
.post.hi h6,.post.hi .more{color:var(--navy)}
.post.hi{border-bottom:3px solid var(--navy)}

/* footer */
.footer{top:3220px;left:0;width:1200px;height:344px;background:var(--footer);color:#bdbdbd}
.footer h4{font-size:13.5px;font-weight:700;color:var(--white);letter-spacing:.5px}
.footer .about{left:188px;top:86px;width:320px;font-size:9.5px;line-height:14px;color:#aaa}
.field{font-size:8.5px;color:#888;border-bottom:1px solid #444;padding-bottom:8px}
.col h5{font-size:10px;font-weight:700;color:var(--white);margin-bottom:12px}
.col li{list-style:none;font-size:9px;color:#9e9e9e;line-height:15.5px}
.foot-rule{left:188px;top:273px;width:826px;border-top:1px solid #3a3a3a}
.foot-small{top:300px;font-size:8.5px;color:#888}
</style>
</head>
<body>

<!-- top bar -->
<header class="abs topbar">
  <div class="abs item" style="left:190px">
    <svg width="11" height="9" viewBox="0 0 11 9"><rect x=".5" y=".5" width="10" height="8" fill="none" stroke="#aaa"/><path d="M.5 .5 5.5 5 10.5 .5" fill="none" stroke="#aaa"/></svg>
    hello@brenlith.au
  </div>
  <div class="abs item" style="left:374px">
    <svg width="10" height="10" viewBox="0 0 10 10"><path d="M2 0h2l1 3-1.5 1a6 6 0 0 0 2.5 2.5L7 5l3 1v2a2 2 0 0 1-2 2A8 8 0 0 1 0 2a2 2 0 0 1 2-2z" fill="#aaa"/></svg>
    +61 2 5550 1842
  </div>
  <div class="abs item" style="left:843px">English
    <svg width="7" height="5" viewBox="0 0 7 5"><path d="M0 0l3.5 4L7 0" fill="none" stroke="#aaa"/></svg>
  </div>
  <div class="abs social-dots"><span></span><span></span><span></span><span></span><span></span></div>
</header>

<!-- navigation -->
<nav class="abs nav">
  <div class="abs logo"><b>Brenlith</b> IT Consultancy</div>
  <div class="abs menu active" style="left:562px">Home</div>
  <div class="abs menu" style="left:626px">About Us</div>
  <div class="abs menu" style="left:704px">Portfolio</div>
  <div class="abs menu" style="left:782px">Blog</div>
  <div class="abs menu" style="left:838px">Pricing</div>
  <div class="abs menu" style="left:904px">Contact</div>
  <svg class="abs" style="left:995px;top:25px" width="15" height="15" viewBox="0 0 15 15"><circle cx="6" cy="6" r="5" fill="none" stroke="#999" stroke-width="1.4"/><path d="M10 10l4 4" stroke="#999" stroke-width="1.4"/></svg>
</nav>

<!-- hero -->
<section class="abs hero" role="img" aria-label="Photograph of a smiling businesswoman on the phone in a bright office"></section>
<h1 class="abs hero-kicker">We are an IT services company</h1>
<h2 class="abs hero-title">Focused strongly on cloud</h2>
<p class="abs hero-text">We help companies sustainably embrace and reap the benefits of cloud platforms, through transforming practices, skills and technology using DevOps and Security practices.</p>
<div class="abs btn hero-btn">GET STARTED NOW</div>
<svg class="abs hero-arrow" width="34" height="34" viewBox="0 0 34 34"><circle cx="17" cy="17" r="15.5" fill="none" stroke="#fff" stroke-width="2"/><path d="M14 10l7 7-7 7" fill="none" stroke="#fff" stroke-width="2"/></svg>
<div class="abs hero-dots"><span style="background:#bbb"></span></div>

<!-- welcome -->
<section class="abs welcome">
  <h2 class="abs h2">Welcome to Our Site</h2>
  <p class="abs">Lorem ipsum dolor sit amet, consectetuer adipiscing elit, sed diam nonummy nibh euismod tincidunt ut laoreet dolore magna aliquam erat volutpat. Ut wisi enim ad minim veniam, quis nostrud exerci tation ullamcorper suscipit lobortis nisl ut aliquip ex ea commodo consequat. Duis autem vel eum iriure dolor in hendrerit in vulputate velit esse molestie consequat, vel illum dolore eu feugiat nulla facilisis at vero eros et accumsan et iusto odio dignissim qui blandit praesent luptatum zzril delenit augue duis dolore te feugait nulla facilisi. Nam liber tempor cum soluta nobis eleifend option congue nihil imperdiet doming id quod mazim placerat facer possim assum.</p>
  <div class="abs btn dark-btn">LEARN MORE</div>
  <div class="abs phone-back"><div class="scr"></div></div>
  <div class="abs phone-front"><div class="scr" role="img" aria-label="Photo of a woman using a smartphone"></div></div>
</section>

<!-- services -->
<section class="abs services">
  <h2 class="abs h2">Services</h2>
  <div class="abs svc" style="left:188px">
    <div class="brand"><i style="background:var(--orange);border-radius:50%"></i>QNT</div>
    <p>Nam liber tempor cum soluta nobis eleifend option congue nihil imperdiet doming id quod mazim.</p>
    <div class="more">Read More ›</div>
  </div>
  <div class="abs svc" style="left:399px">
    <div class="brand"><i style="background:var(--azure)"></i>Vantrel Skyline</div>
    <p>Lorem ipsum dolor sit amet, adipiscing elit, sed diam nonummy nibh euismod tincidunt ut laoreet.</p>
    <div class="more on">Read More ›</div>
  </div>
  <div class="abs svc" style="left:613px">
    <div class="brand"><i style="background:#e9b92c;border-radius:50%"></i>Horvik Vapor</div>
    <p>Nam liber tempor cum soluta nobis eleifend option congue nihil imperdiet doming id quod mazim.</p>
    <div class="more">Read More ›</div>
  </div>
  <div class="abs svc" style="left:822px">
    <div class="brand"><i style="background:#4a8f4f"></i>Quorra Builders</div>
    <p>Lorem ipsum dolor sit amet, adipiscing elit, sed diam nonummy nibh euismod tincidunt ut laoreet.</p>
    <div class="more">Read More ›</div>
  </div>
</section>

<!-- call to action band -->
<section class="abs band">
  <h3 class="abs">Lorem ipsum dolor sit</h3>
  <p class="abs">Lorem ipsum dolor sit amet, consectetuer adipiscing elit, sed diam nonummy nibh euismod tincidunt ut laoreet dolore magna aliquam erat volutpat. Ut wisi enim ad minim veniam, quis nostrud exerci tation ullamcorper suscipit lobortis nisl ut aliquip ex ea commodo consequat.</p>
  <div class="abs btn">CONTACT NOW</div>
</section>

<!-- core features -->
<section class="abs features">
  <div class="abs our">Our</div>
  <div class="abs ttl">CORE <b>FEATURES</b></div>
  <div class="abs fphone"><div class="spk"></div><div class="scr" role="img" aria-label="Photo of a hand holding a phone showing a weather screen"></div><div class="home"></div></div>

  <div class="abs feat left" style="top:260px"><h4>Lorem ipsum</h4><p>Lorem ipsum dolor sit amet, consectetuer adipiscing elit.</p></div>
  <div class="abs feat left hi" style="top:346px"><h4>Ipsum sit</h4><p>Duis autem vel eum iriure dolor in hendrerit in vulputate velit esse.</p></div>
  <div class="abs feat left" style="top:422px"><h4>Lorem ipsum dolorsit</h4><p>Ut wisi enim ad minim veniam, quis nostrud exerci tation.</p></div>

  <svg class="abs tri" style="left:405px;top:256px" viewBox="0 0 46 46"><path d="M23 4L43 40H3z" fill="none" stroke="#fff" stroke-width="2"/><rect x="19" y="24" width="8" height="8" fill="none" stroke="#fff" stroke-width="1.5"/></svg>
  <svg class="abs tri" style="left:405px;top:340px" viewBox="0 0 46 46"><path d="M23 4L43 40H3z" fill="none" stroke="var(--cyan)" stroke-width="2"/><rect x="19" y="21" width="8" height="12" rx="1" fill="none" stroke="var(--cyan)" stroke-width="1.5"/></svg>
  <svg class="abs tri" style="left:405px;top:416px" viewBox="0 0 46 46"><path d="M23 4L43 40H3z" fill="none" stroke="#fff" stroke-width="2"/><path d="M17 31h12a3 3 0 0 0 0-6 5 5 0 0 0-9-1 3.5 3.5 0 0 0-3 7z" fill="#fff"/></svg>

  <svg class="abs tri" style="left:752px;top:256px" viewBox="0 0 46 46"><path d="M23 4L43 40H3z" fill="none" stroke="#fff" stroke-width="2"/><path d="M15 30l8-8 8 8" fill="none" stroke="#fff" stroke-width="1.5"/></svg>
  <svg class="abs tri" style="left:752px;top:340px" viewBox="0 0 46 46"><path d="M23 4L43 40H3z" fill="none" stroke="#fff" stroke-width="2"/><path d="M18 24h10M18 28h10M18 32h10" stroke="#fff" stroke-width="1.5"/></svg>
  <svg class="abs tri" style="left:752px;top:416px" viewBox="0 0 46 46"><path d="M23 4L43 40H3z" fill="none" stroke="#fff" stroke-width="2"/><circle cx="23" cy="28" r="4" fill="none" stroke="#fff" stroke-width="1.5"/></svg>

  <div class="abs feat right" style="top:260px"><h4>Contatnry Popilar</h4><p>Lorem ipsum dolor sit amet, consectetuer adipiscing elit.</p></div>
  <div class="abs feat right" style="top:346px"><h4>Popilar sit</h4><p>Duis autem vel eum iriure dolor in hendrerit in vulputate velit esse.</p></div>
  <div class="abs feat right" style="top:422px"><h4>Amit lorem sit</h4><p>Ut wisi enim ad minim veniam, quis nostrud exerci tation.</p></div>
</section>

<!-- pricing -->
<section class="abs pricing">
  <h2 class="abs h2">Our Pricing.</h2>
  <p class="abs lead">Lorem ipsum dolor sit amet, consectetuer adipiscing elit, sed diam nonummy nibh euismod tincidunt ut laoreet dolore magna aliquam erat volutpat.</p>

  <div class="abs plan" style="left:188px;top:188px;width:275px;height:394px">
    <div class="head" style="height:55px;background:var(--gray-head)"><h5>Standart</h5><span>Monthly Plan</span></div>
    <div class="price"><small>$</small>29<sup>99</sup></div>
    <ul><li>10GB Disk Space</li><li>10GB Monthly Bandwidth</li><li>Unlimited Users</li><li>150 Domains</li><li>450 Email Accounts</li><li>Automatic Cloud Backups</li></ul>
    <div class="btn" style="background:var(--gray-head);margin-top:16px">SIGN UP NOW!</div>
  </div>
  <div class="abs plan mid" style="left:463px;top:159px;width:276px;height:452px;z-index:2;box-shadow:0 4px 20px rgba(0,0,0,.16)">
    <div class="head" style="height:84px;background:var(--cyan)"><h5>Unlimited</h5><span>Monthly Plan</span></div>
    <div class="price"><small>$</small>199<sup>99</sup></div>
    <ul><li>10GB Disk Space</li><li>10GB Monthly Bandwidth</li><li>Unlimited Users</li><li>150 Domains</li><li>450 Email Accounts</li><li>Automatic Cloud Backups</li></ul>
    <div class="btn" style="background:var(--cyan);margin-top:20px">SIGN UP NOW!</div>
  </div>
  <div class="abs plan" style="left:739px;top:188px;width:275px;height:394px">
    <div class="head" style="height:55px;background:var(--dark-head)"><h5>Premium</h5><span>Monthly Plan</span></div>
    <div class="price"><small>$</small>99<sup>99</sup></div>
    <ul><li>10GB Disk Space</li><li>10GB Monthly Bandwidth</li><li>Unlimited Users</li><li>150 Domains</li><li>450 Email Accounts</li><li>Automatic Cloud Backups</li></ul>
    <div class="btn" style="background:var(--dark-head);margin-top:16px">SIGN UP NOW!</div>
  </div>
</section>

<!-- blog -->
<section class="abs blog">
  <h2 class="abs h2">From Blog.</h2>
  <div class="abs circ" style="left:976px;top:66px"></div>
  <div class="abs circ" style="left:997px;top:66px;border-color:var(--cyan)"></div>

  <article class="abs post" style="left:188px">
    <div class="img" role="img" aria-label="Photo of business people meeting at a table" style="background:linear-gradient(135deg,#c9cdd3,#6b7480 55%,#2f3540)"><span class="tag"></span></div>
    <div class="meta"><span>By John Doe</span><span>Date: 08.09.2015</span><span>18 Comments</span></div>
    <h6>Lorem ipsum dolor sit amet</h6>
    <p>Nam liber tempor cum soluta nobis eleifend option congue nihil imperdiet doming id quod mazim.</p>
    <div class="more">Read More ›</div>
  </article>
  <article class="abs post hi" style="left:470px">
    <div class="img" role="img" aria-label="Blue-tinted photo of a conference audience" style="background:linear-gradient(135deg,#4d6d9c,#2c4d80 60%,#1d3766)"><span class="tag" style="background:rgba(20,60,120,.85)"></span></div>
    <div class="meta"><span>By John Doe</span><span>Date: 08.09.2015</span><span>18 Comments</span></div>
    <h6>Claritas est etiam processus</h6>
    <p>Lorem ipsum dolor sit amet, adipiscing elit, sed diam nonummy nibh euismod tincidunt ut.</p>
    <div class="more">Read More ›</div>
  </article>
  <article class="abs post" style="left:751px">
    <div class="img" role="img" aria-label="Photo of a business team in discussion" style="background:linear-gradient(135deg,#d6d9de,#7d8794 55%,#38404c)"><span class="tag"></span></div>
    <div class="meta"><span>By John Doe</span><span>Date: 08.09.2015</span><span>18 Comments</span></div>
    <h6>Lorem ipsum dolor sit amet</h6>
    <p>Nam liber tempor cum soluta nobis eleifend option congue nihil imperdiet doming id quod mazim.</p>
    <div class="more">Read More ›</div>
  </article>
</section>

<!-- footer -->
<footer class="abs footer">
  <h4 class="abs" style="left:188px;top:52px">BRENLITH IT CONSULTANCY</h4>
  <p class="abs about">Vestibulum quis nulla facilisis ipsum aliquam semper nec et dui. Phasellus ipsum ligula, sodales at faucibus at, fringilla at lorem.</p>
  <div class="abs field" style="left:188px;top:140px;width:150px">EMAIL</div>
  <div class="abs field" style="left:350px;top:140px;width:150px">SUBJECT</div>
  <div class="abs field" style="left:188px;top:168px;width:312px">MESSAGE</div>
  <div class="abs" style="left:188px;top:246px;font-size:8.5px;color:#aaa">SEND ›</div>

  <div class="abs col" style="left:611px;top:54px"><h5>LINKS</h5><ul><li>Home</li><li>About</li><li>Services</li><li>Menu</li><li>Restaurants</li><li>Work Hours</li><li>Café Hours</li></ul></div>
  <div class="abs col" style="left:751px;top:54px"><h5>FRIENDS</h5><ul><li>Home</li><li>About</li><li>Services</li><li>Menu</li><li>Restaurants</li></ul></div>
  <div class="abs col" style="left:893px;top:54px"><h5>SOCIAL</h5><ul><li>Linkfeed</li><li>Chirper</li><li>Codehub</li><li>Pinboard</li><li>Circles</li><li>Shotbox</li><li>Snapline</li><li>Others</li></ul></div>

  <div class="abs foot-rule"></div>
  <div class="abs foot-small" style="left:188px">© 2016 Your Company. All rights reserved</div>
  <div class="abs foot-small" style="left:808px">TERMS</div>
  <div class="abs foot-small" style="left:855px">PRIVACY POLICY</div>
  <div class="abs foot-small" style="left:941px">CONTACT</div>
  <div class="abs foot-small" style="left:998px">JOB</div>
</footer>

</body>
</html>
```